Financial investment calculator report for real estae - layout & design

I am looking to Create a web report utilizing the attached information. It is an investment calculator report that will be customized report based on an online calculator. Therefore the report will need to be designed in a manner that a backend developer will be able to build off of.

The report will need to be web based but also printed in PDF format. The report will need to include the calculation format as well as be templeted to add a report user unique profile information like Headshot, Business Logo, Name, Telephone number, email etc.

The report should be modern and clean and easy to read and use a modern clean template design. It should be able to be easily color customized by the end user to produce templets in Red, Blue, Green, and Greyscale.

The report should be no more than 3 pages total with out breaking up the sections.

Section One - Cover sheet including agent bio info, Report Title and property address (both prominent), 400 Character space for property description, Property Pictures (3), and a google Maps integration image showing property location, It should also have room for about 100 words for a text disclaimer. (I will provide text soon)

Section Two - Inputs from the calculator

Section 3 - The Four Benefits & Rates of Return

Once I have a completed/approved form I will have about a half dozen forms/reports that will need to be laid out with a similar aesthetic.

Feel free to ask me any questions. Thank You
Milo

Target Market(s)

This report will be produced by real estate agents forvtheir investor clients. It should denote professionalism

Font styles to use
Sans Serif

Colors
0054AA
0677BA
7BADD7
CADEEF
E8F1F8
00AB8E
00BBA5
67D7C9
C6EFE9
E9F9F6
EB3D1F
EC4F4E
F09395
F8D3D4
FCEDEE

```html
<!DOCTYPE html>
<html lang="en">
<head>
<meta charset="utf-8">
<title>Investment Analysis Report Templates</title>
<link rel="stylesheet" href="https://fonts.googleapis.com/css2?family=Sora:wght@400;500;600;700&display=swap">
<style>
:root{
  --backdrop:#bdbdbd;
  --ink:#3a3a3a;
  --muted:#555;
  --line:#e2e2e2;
  --card:#efefef;
}
.theme-blue{--brand:#1257a8;--pale:#dfe4f2;}
.theme-red{--brand:#a61e24;--pale:#f2e0dc;}
html,body{margin:0;padding:0;width:1026px;height:1200px;overflow:hidden;background:var(--backdrop);}
.stage{position:relative;width:1772px;height:2072px;transform:scale(0.579007);transform-origin:0 0;font-family:"Sora",sans-serif;color:var(--ink);}
.page{position:absolute;width:422px;height:548px;background:#fff;overflow:hidden;}
.col-1{left:190px}.col-2{left:670px}.col-3{left:1150px}
.row-1{top:175px}.row-2{top:787px}.row-3{top:1404px}

.band{position:absolute;left:0;top:0;width:100%;background:var(--brand);}
.band-tall{height:94px}
.band-short{height:41px}
.band-grey{height:94px;background:#e8e8e8}
.topline{position:absolute;top:5px;left:12px;right:14px;display:flex;justify-content:space-between;font-size:4.5px;color:rgba(255,255,255,.75);z-index:2}
.band-grey + .topline,.topline.dark{color:#444}
.footer{position:absolute;bottom:5px;left:12px;right:18px;display:flex;justify-content:space-between;font-size:4.5px;color:#333}

.brand-name{position:absolute;display:flex;align-items:center;gap:6px;font-weight:600;color:#fff;letter-spacing:1.5px}
.brand-name .dot{width:28px;height:28px;border:1.6px solid currentColor;border-radius:50%;box-sizing:border-box}
.brand-cover{left:35px;top:32px;font-size:17px}
.brand-center{left:0;right:0;top:29px;justify-content:center;font-size:21px;color:var(--brand)}
.brand-center .dot{width:38px;height:38px;border-width:2px}
.brand-mark{position:absolute;left:29px;top:16px;width:18px;height:18px;border:1.4px solid #fff;border-radius:50%;box-sizing:border-box}

.title{position:absolute;font-weight:600;font-size:20px;line-height:23px;color:#444}
.title .addr{display:block;color:var(--brand);font-weight:700}
.title .sub{display:block;color:var(--brand);font-size:9.5px;line-height:13px;font-weight:400}
.title-left{left:40px;top:118px}
.title-center{left:0;right:0;top:124px;text-align:center}

.label{font-size:5.5px;letter-spacing:1.4px;color:#666;font-weight:500;text-transform:uppercase}
.about{position:absolute;left:40px;top:199px;width:210px}
.about p{margin:6px 0 0;font-size:6.6px;line-height:9px;color:#222}

.agent-card{position:absolute;left:279px;top:40px;width:108px;height:161px;background:var(--card);border-radius:5px;text-align:center;font-size:6.6px;line-height:10px;color:#666}
.avatar{display:block;border-radius:50%;border:1.4px solid var(--brand);background:radial-gradient(circle at 50% 40%,#c89b7f 0 30%,#2d3a55 31% 100%);box-sizing:border-box}
.agent-card .avatar{width:66px;height:66px;margin:15px auto 10px}
.agent-card .role{color:var(--brand);font-weight:700;font-size:5.5px;letter-spacing:1.2px}
.agent-card .name{font-weight:600;color:#444}

.photos{position:absolute;display:flex}
.photo{display:block}
.photos-cover{left:35px;top:262px;gap:12px}
.photos-cover .photo{width:110px;height:99px;border-radius:4px;border:1.5px solid #ddd;box-sizing:border-box}
.photos-alt{left:35px;top:211px;gap:6px}
.photos-alt .photo{width:113px;height:90px}
.ph-house{background:linear-gradient(180deg,#b6a3c8 0%,#5a6894 45%,#2b3452 75%,#8a8f9a 100%)}
.ph-blue{background:linear-gradient(135deg,#1c5f9c 0%,#1d4f84 55%,#5a4232 100%)}
.ph-living{background:linear-gradient(180deg,#cfd5d3 0%,#b8c0c0 60%,#9aa1a2 100%)}
.ph-kitchen{background:linear-gradient(180deg,#e6e4df 0%,#bfbab3 60%,#4e4540 100%)}
.ph-dining{background:linear-gradient(180deg,#d9cfc4 0%,#b9a795 55%,#7d6a5b 100%)}
.map{position:absolute;background:linear-gradient(135deg,#f1f1ef 0%,#e9ede6 55%,#eef0f2 100%);border-radius:6px;border:1px solid #e0e0e0;box-sizing:border-box}
.map-cover{left:33px;top:375px;width:355px;height:83px}
.map-alt{left:206px;top:320px;width:180px;height:103px}

.disclaimer-band{position:absolute;left:0;top:471px;width:100%;height:54px;background:var(--brand);color:#fff;box-sizing:border-box;padding:8px 39px 0}
.disclaimer-band .label{color:rgba(255,255,255,.85)}
.disclaimer-band p{margin:8px 0 0;font-size:6.3px;line-height:8.6px}

.box{position:absolute;top:450px;height:68px;background:var(--card);border-radius:6px;box-sizing:border-box;font-size:6.6px;line-height:9.5px;color:#555}
.box-agent{left:35px;width:155px;padding:12px 0 0 103px}
.box-agent .avatar{position:absolute;left:12px;top:7px;width:54px;height:54px}
.box-agent .name{font-weight:600;color:#444}
.box-disc{left:198px;width:188px;padding:12px 14px}
.box-disc strong{display:block;font-weight:600;color:#444}

.heading{position:absolute;left:33px;top:62px;font-size:15.5px;font-weight:700;color:var(--brand);margin:0}
.heading + .lead,.lead{position:absolute;left:33px;font-size:7.5px;color:#444;margin:0}

.sheet{position:absolute;left:34px;width:353px;font-size:4.4px;color:#333}
.sheet .head{background:var(--pale);height:10px;line-height:10px;padding-left:5px;font-weight:600}
.sheet .r{display:grid;height:10.2px;line-height:10.2px;border-bottom:.5px solid var(--line)}
.sheet .r span{padding-left:5px;border-right:.5px solid #eee;white-space:nowrap;overflow:hidden}
.sheet .r span:last-child{border-right:0}
.sheet .r.total{background:var(--pale);font-weight:700;font-size:5px;border:0}
.sheet .r.bold{font-weight:700}
.g4{grid-template-columns:116px 56px 80px 1fr}
.g5{grid-template-columns:101px 60px 55px 65px 1fr}
.g3{grid-template-columns:101px 150px 1fr}
.g3b{grid-template-columns:106px 180px 1fr}
</style>
</head>
<body>
<div class="stage">

<!-- ===== Blue cover ===== -->
<section class="page theme-blue col-1 row-1">
  <div class="band band-tall"></div>
  <div class="topline"><span>5/30/23, 10:23 AM</span><span>Investment Analysis</span></div>
  <div class="brand-name brand-cover"><span class="dot"></span>MERIDIAN REALTY</div>
  <div class="agent-card">
    <span class="avatar" role="img" aria-label="Agent headshot"></span>
    <div class="role">AGENT</div>
    <div class="name">Dana Whitlow</div>
    <div>admin1</div><div>(555) 014-2290</div><div>dana@meridianrealty.example</div>
  </div>
  <h1 class="title title-left">Investment Analysis<span class="addr">412 Larkfield</span><span class="sub">15-Plex of 1bd/1bth Apartments</span></h1>
  <div class="about"><div class="label">About the property</div><p>Lorem ipsum is a placeholder text commonly used to demonstrate the visual form of a document or a typeface without relying on meaningful content.</p></div>
  <div class="photos photos-cover">
    <span class="photo ph-house" role="img" aria-label="Property exterior at dusk"></span>
    <span class="photo ph-blue" role="img" aria-label="Interior with blue feature wall"></span>
    <span class="photo ph-living" role="img" aria-label="Living room interior"></span>
  </div>
  <div class="map map-cover" role="img" aria-label="Map showing property location"></div>
  <div class="disclaimer-band"><div class="label">Disclaimer</div><p>In publishing and graphic design, Lorem ipsum is a placeholder text commonly used to demonstrate the visual form of a document or a typeface without relying on meaningful content. Lorem ipsum may be used as a placeholder before final copy is available.</p></div>
  <div class="footer"><span>https://reports.example.com/r/115</span><span>1/3</span></div>
</section>

<!-- ===== Blue calculator ===== -->
<section class="page theme-blue col-2 row-1">
  <div class="band band-short"></div>
  <div class="topline"><span>5/30/23, 10:23 AM</span><span>Investment Analysis</span></div>
  <span class="brand-mark"></span>
  <h2 class="heading">A: Data from Calculator</h2>
  <p class="lead" style="top:82px">Lorem ipsum sit amet.</p>
  <div class="sheet" style="top:100px">
    <div class="head">Property Address: 412 Larkfield</div>
    <div class="r g4"><span>Financing</span><span>20% Down</span><span>20 Year Conventional</span><span></span></div>
    <div class="r g4"><span>Purchase Price</span><span></span><span></span><span>$1690000</span></div>
    <div class="r g4"><span>Down Payment (Cash Invested)</span><span></span><span></span><span>$338000</span></div>
    <div class="r g4"><span>Amount Financed</span><span></span><span></span><span>$1352000</span></div>
    <div class="r g4"><span>Needed Capital Improvements Est.</span><span></span><span></span><span>$0</span></div>
    <div class="r g4"><span>Est. Closing Costs</span><span></span><span></span><span>$3000</span></div>
    <div class="r g4"><span>CASH Invested (Down Pmt. + Closing Costs)</span><span></span><span></span><span>$341000</span></div>
    <div class="r g4"><span></span><span>Rate</span><span>Terms (yrs)</span><span></span></div>
    <div class="r g4"><span></span><span>7%</span><span>20</span><span></span></div>
    <div class="r g4 total"><span>Monthly P&amp;I</span><span></span><span></span><span>$10482</span></div>
  </div>
  <div class="sheet" style="top:229px">
    <div class="head">Depreciation (first year): (assumes 80%/20%)</div>
    <div class="r g5"><span></span><span></span><span>Est. Value</span><span>Yearly Rate</span><span></span></div>
    <div class="r g5"><span>Land Cost</span><span>0 years</span><span>$338000</span><span>0%</span><span>$0</span></div>
    <div class="r g5"><span>Personal Property Cost</span><span>5 years</span><span>$45000</span><span>20%</span><span>$9000</span></div>
    <div class="r g5"><span>Building Cost: 27.5 Years</span><span>27.5 years</span><span>$1262000</span><span>3.48%</span><span>$43918</span></div>
    <div class="r g5"><span>Land Improvement Cost</span><span>15 years</span><span>$45000</span><span>5%</span><span>$2250</span></div>
    <div class="r g5 total"><span>Total Depreciation</span><span></span><span></span><span></span><span>$55168</span></div>
  </div>
  <div class="sheet" style="top:326px">
    <div class="head">Income</div>
    <div class="r g3"><span>Annual Rent</span><span></span><span>$170000</span></div>
    <div class="r g3"><span>Other Income</span><span></span><span>$0</span></div>
    <div class="r g3"><span>Less Vacancy</span><span>est. 5% of annual rent</span><span>$0</span></div>
    <div class="r g3 total"><span>Gross Operating</span><span></span><span>$170000</span></div>
  </div>
  <div class="sheet" style="top:397px">
    <div class="head">Expenses</div>
    <div class="r g3"><span>Real Estate Tax</span><span></span><span>$27439</span></div>
    <div class="r g3"><span>Insurance: est. $349</span><span></span><span>$3492</span></div>
    <div class="r g3"><span>Association Dues/HOAs</span><span>est. 5% of annual rent</span><span>$0</span></div>
    <div class="r g3"><span>Management</span><span></span><span>$0</span></div>
    <div class="r g3"><span>Utilities</span><span></span><span>$9192</span></div>
    <div class="r g3"><span>Advertising</span><span></span><span>$0</span></div>
    <div class="r g3"><span>Maintenance</span><span></span><span>$0</span></div>
    <div class="r g3"><span>Miscellaneous1</span><span></span><span>$0</span></div>
    <div class="r g3 total"><span>Total Expenses</span><span></span><span>$40123</span></div>
  </div>
  <div class="footer"><span>https://reports.example.com/r/115</span><span>2/3</span></div>
</section>

<!-- ===== Blue benefits ===== -->
<section class="page theme-blue col-3 row-1">
  <div class="band band-short"></div>
  <div class="topline"><span>5/30/23, 10:23 AM</span><span>Investment Analysis</span></div>
  <span class="brand-mark"></span>
  <h2 class="heading">B: The Four Benefits</h2>
  <p class="lead" style="top:82px">Lorem ipsum sit amet.</p>
  <div class="sheet" style="top:100px">
    <div class="head">Cash Flow Before Tax</div>
    <div class="r g3b"><span>Gross Operating Income</span><span></span><span>$170000</span></div>
    <div class="r g3b"><span>Operating Expenses</span><span></span><span>$40123</span></div>
    <div class="r g3b"><span>Net Operating Income</span><span></span><span>$129877</span></div>
    <div class="r g3b"><span>Annual Debt Service (Monthly P&amp;I x 12)</span><span></span><span>$125784</span></div>
    <div class="r g3b total"><span>Cash Flow Before Tax</span><span></span><span>$4092</span></div>
  </div>
  <div class="sheet" style="top:181px">
    <div class="head">Principal Reduction</div>
    <div class="r g3b"><span>Annual Debt Service</span><span></span><span>$125784</span></div>
    <div class="r g3b"><span>Interest (first year)</span><span></span><span>-$93621</span></div>
    <div class="r g3b"><span>Principal Reduction</span><span></span><span>$32163</span></div>
    <div class="r g3b total"><span>Principal Reduction</span><span></span><span>$32163</span></div>
  </div>
  <div class="sheet" style="top:254px">
    <div class="head">Taxes Paid/Saved</div>
    <div class="r g3b"><span>Net Operating Income</span><span></span><span>$129877</span></div>
    <div class="r g3b"><span>Interest paid in first year</span><span></span><span>$93621</span></div>
    <div class="r g3b"><span>Taxable Income</span><span></span><span>$55168</span></div>
    <div class="r g3b"><span>Tax Bracket</span><span>28%</span><span>$16912</span></div>
    <div class="r g3b bold"><span>Taxes Saved</span><span></span><span>$5295</span></div>
    <div class="r g3b"><span>Appreciation</span><span>Estimate of Appreciation</span><span>$0</span></div>
    <div class="r g3b"><span></span><span></span><span>I can't predict the future</span></div>
  </div>
  <h2 class="heading" style="top:361px">C: Rates of Return</h2>
  <p class="lead" style="top:381px">Lorem ipsum sit amet.</p>
  <div class="sheet" style="top:396px">
    <div class="head">Return on Investment without Appreciation</div>
    <div class="r g3b"><span>Cash Flow before Tax + Principal Reduction + Tax Saved</span><span></span><span>$30961</span></div>
    <div class="r g3b"><span>Cash Invested</span><span></span><span>$341000</span></div>
    <div class="r g3b total"><span>ROI w/o Appreciation:</span><span></span><span>9.08%</span></div>
  </div>
  <div class="sheet" style="top:457px">
    <div class="head">Return on Investment without Appreciation</div>
    <div class="r g3b"><span>Net Operating Income</span><span></span><span>$129877</span></div>
    <div class="r g3b"><span>Purchase Cost</span><span></span><span>$1690000</span></div>
    <div class="r g3b total"><span>ROI w/o Appreciation:</span><span></span><span>7.69%</span></div>
  </div>
  <div class="footer"><span>https://reports.example.com/r/115</span><span>3/3</span></div>
</section>

<!-- ===== Red cover ===== -->
<section class="page theme-red col-1 row-2">
  <div class="band band-tall"></div>
  <div class="topline"><span>5/30/23, 10:23 AM</span><span>Investment Analysis</span></div>
  <div class="brand-name brand-cover"><span class="dot"></span>MERIDIAN REALTY</div>
  <div class="agent-card">
    <span class="avatar" role="img" aria-label="Agent headshot"></span>
    <div class="role">AGENT</div>
    <div class="name">Dana Whitlow</div>
    <div>admin1</div><div>(555) 014-2290</div><div>dana@meridianrealty.example</div>
  </div>
  <h1 class="title title-left">Investment Analysis<span class="addr">412 Larkfield</span><span class="sub">15-Plex of 1bd/1bth Apartments</span></h1>
  <div class="about"><div class="label">About the property</div><p>Lorem ipsum is a placeholder text commonly used to demonstrate the visual form of a document or a typeface without relying on meaningful content.</p></div>
  <div class="photos photos-cover">
    <span class="photo ph-house" role="img" aria-label="Property exterior at dusk"></span>
    <span class="photo ph-blue" role="img" aria-label="Interior with blue feature wall"></span>
    <span class="photo ph-living" role="img" aria-label="Living room interior"></span>
  </div>
  <div class="map map-cover" role="img" aria-label="Map showing property location"></div>
  <div class="disclaimer-band"><div class="label">Disclaimer</div><p>In publishing and graphic design, Lorem ipsum is a placeholder text commonly used to demonstrate the visual form of a document or a typeface without relying on meaningful content. Lorem ipsum may be used as a placeholder before final copy is available.</p></div>
  <div class="footer"><span>https://reports.example.com/r/115</span><span>1/3</span></div>
</section>

<!-- ===== Red calculator ===== -->
<section class="page theme-red col-2 row-2">
  <div class="band band-short"></div>
  <div class="topline"><span>5/30/23, 10:23 AM</span><span>Investment Analysis</span></div>
  <span class="brand-mark"></span>
  <h2 class="heading">A: Data from Calculator</h2>
  <p class="lead" style="top:82px">Lorem ipsum sit amet.</p>
  <div class="sheet" style="top:100px">
    <div class="head">Property Address: 412 Larkfield</div>
    <div class="r g4"><span>Financing</span><span>20% Down</span><span>20 Year Conventional</span><span></span></div>
    <div class="r g4"><span>Purchase Price</span><span></span><span></span><span>$1690000</span></div>
    <div class="r g4"><span>Down Payment (Cash Invested)</span><span></span><span></span><span>$338000</span></div>
    <div class="r g4"><span>Amount Financed</span><span></span><span></span><span>$1352000</span></div>
    <div class="r g4"><span>Needed Capital Improvements Est.</span><span></span><span></span><span>$0</span></div>
    <div class="r g4"><span>Est. Closing Costs</span><span></span><span></span><span>$3000</span></div>
    <div class="r g4"><span>CASH Invested (Down Pmt. + Closing Costs)</span><span></span><span></span><span>$341000</span></div>
    <div class="r g4"><span></span><span>Rate</span><span>Terms (yrs)</span><span></span></div>
    <div class="r g4"><span></span><span>7%</span><span>20</span><span></span></div>
    <div class="r g4 total"><span>Monthly P&amp;I</span><span></span><span></span><span>$10482</span></div>
  </div>
  <div class="sheet" style="top:229px">
    <div class="head">Depreciation (first year): (assumes 80%/20%)</div>
    <div class="r g5"><span></span><span></span><span>Est. Value</span><span>Yearly Rate</span><span></span></div>
    <div class="r g5"><span>Land Cost</span><span>0 years</span><span>$338000</span><span>0%</span><span>$0</span></div>
    <div class="r g5"><span>Personal Property Cost</span><span>5 years</span><span>$45000</span><span>20%</span><span>$9000</span></div>
    <div class="r g5"><span>Building Cost: 27.5 Years</span><span>27.5 years</span><span>$1262000</span><span>3.48%</span><span>$43918</span></div>
    <div class="r g5"><span>Land Improvement Cost</span><span>15 years</span><span>$45000</span><span>5%</span><span>$2250</span></div>
    <div class="r g5 total"><span>Total Depreciation</span><span></span><span></span><span></span><span>$55168</span></div>
  </div>
  <div class="sheet" style="top:326px">
    <div class="head">Income</div>
    <div class="r g3"><span>Annual Rent</span><span></span><span>$170000</span></div>
    <div class="r g3"><span>Other Income</span><span></span><span>$0</span></div>
    <div class="r g3"><span>Less Vacancy</span><span>est. 5% of annual rent</span><span>$0</span></div>
    <div class="r g3 total"><span>Gross Operating</span><span></span><span>$170000</span></div>
  </div>
  <div class="sheet" style="top:397px">
    <div class="head">Expenses</div>
    <div class="r g3"><span>Real Estate Tax</span><span></span><span>$27439</span></div>
    <div class="r g3"><span>Insurance: est. $349</span><span></span><span>$3492</span></div>
    <div class="r g3"><span>Association Dues/HOAs</span><span>est. 5% of annual rent</span><span>$0</span></div>
    <div class="r g3"><span>Management</span><span></span><span>$0</span></div>
    <div class="r g3"><span>Utilities</span><span></span><span>$9192</span></div>
    <div class="r g3"><span>Advertising</span><span></span><span>$0</span></div>
    <div class="r g3"><span>Maintenance</span><span></span><span>$0</span></div>
    <div class="r g3"><span>Miscellaneous1</span><span></span><span>$0</span></div>
    <div class="r g3 total"><span>Total Expenses</span><span></span><span>$40123</span></div>
  </div>
  <div class="footer"><span>https://reports.example.com/r/115</span><span>2/3</span></div>
</section>

<!-- ===== Red benefits ===== -->
<section class="page theme-red col-3 row-2">
  <div class="band band-short"></div>
  <div class="topline"><span>5/30/23, 10:23 AM</span><span>Investment Analysis</span></div>
  <span class="brand-mark"></span>
  <h2 class="heading">B: The Four Benefits</h2>
  <p class="lead" style="top:82px">Lorem ipsum sit amet.</p>
  <div class="sheet" style="top:100px">
    <div class="head">Cash Flow Before Tax</div>
    <div class="r g3b"><span>Gross Operating Income</span><span></span><span>$170000</span></div>
    <div class="r g3b"><span>Operating Expenses</span><span></span><span>$40123</span></div>
    <div class="r g3b"><span>Net Operating Income</span><span></span><span>$129877</span></div>
    <div class="r g3b"><span>Annual Debt Service (Monthly P&amp;I x 12)</span><span></span><span>$125784</span></div>
    <div class="r g3b total"><span>Cash Flow Before Tax</span><span></span><span>$4092</span></div>
  </div>
  <div class="sheet" style="top:181px">
    <div class="head">Principal Reduction</div>
    <div class="r g3b"><span>Annual Debt Service</span><span></span><span>$125784</span></div>
    <div class="r g3b"><span>Interest (first year)</span><span></span><span>-$93621</span></div>
    <div class="r g3b"><span>Principal Reduction</span><span></span><span>$32163</span></div>
    <div class="r g3b total"><span>Principal Reduction</span><span></span><span>$32163</span></div>
  </div>
  <div class="sheet" style="top:254px">
    <div class="head">Taxes Paid/Saved</div>
    <div class="r g3b"><span>Net Operating Income</span><span></span><span>$129877</span></div>
    <div class="r g3b"><span>Interest paid in first year</span><span></span><span>$93621</span></div>
    <div class="r g3b"><span>Taxable Income</span><span></span><span>$55168</span></div>
    <div class="r g3b"><span>Tax Bracket</span><span>28%</span><span>$16912</span></div>
    <div class="r g3b bold"><span>Taxes Saved</span><span></span><span>$5295</span></div>
    <div class="r g3b"><span>Appreciation</span><span>Estimate of Appreciation</span><span>$0</span></div>
    <div class="r g3b"><span></span><span></span><span>I can't predict the future</span></div>
  </div>
  <h2 class="heading" style="top:361px">C: Rates of Return</h2>
  <p class="lead" style="top:381px">Lorem ipsum sit amet.</p>
  <div class="sheet" style="top:396px">
    <div class="head">Return on Investment without Appreciation</div>
    <div class="r g3b"><span>Cash Flow before Tax + Principal Reduction + Tax Saved</span><span></span><span>$30961</span></div>
    <div class="r g3b"><span>Cash Invested</span><span></span><span>$341000</span></div>
    <div class="r g3b total"><span>ROI w/o Appreciation:</span><span></span><span>9.08%</span></div>
  </div>
  <div class="sheet" style="top:457px">
    <div class="head">Return on Investment without Appreciation</div>
    <div class="r g3b"><span>Net Operating Income</span><span></span><span>$129877</span></div>
    <div class="r g3b"><span>Purchase Cost</span><span></span><span>$1690000</span></div>
    <div class="r g3b total"><span>ROI w/o Appreciation:</span><span></span><span>7.69%</span></div>
  </div>
  <div class="footer"><span>https://reports.example.com/r/115</span><span>3/3</span></div>
</section>

<!-- ===== Alternate cover, blue ===== -->
<section class="page theme-blue col-1 row-3">
  <div class="band band-grey"></div>
  <div class="topline dark"><span>5/30/23, 10:23 AM</span><span>Investment Analysis</span></div>
  <div class="brand-name brand-center"><span class="dot"></span>MERIDIAN REALTY</div>
  <h1 class="title title-center">Investment Analysis<span class="addr">412 Larkfield</span><span class="sub">15-Plex of 1bd/1bth Apartments</span></h1>
  <div class="photos photos-alt">
    <span class="photo ph-house" role="img" aria-label="Property exterior at dusk"></span>
    <span class="photo ph-kitchen" role="img" aria-label="Kitchen interior"></span>
    <span class="photo ph-dining" role="img" aria-label="Dining area interior"></span>
  </div>
  <div class="about" style="left:38px;top:330px;width:150px"><div class="label">About the property</div><p>Lorem ipsum is a placeholder text commonly used to demonstrate the visual form of a document or a typeface without relying on meaningful content.</p><p>Lorem ipsum is a placeholder text commonly used to demonstrate the visual form of a document or a typeface</p></div>
  <div class="map map-alt" role="img" aria-label="Map showing property location"></div>
  <div class="box box-agent"><span class="avatar" role="img" aria-label="Agent headshot"></span><div class="name">Dana Whitlow</div><div>admin1</div><div>(555) 014-2290</div><div>dana@meridian.example</div></div>
  <div class="box box-disc"><strong>DISCLAIMER</strong>In publishing and graphic design, Lorem ipsum is a placeholder text commonly used to demonstrate the visual form of a document or a typeface</div>
  <div class="footer"><span>https://reports.example.com/r/115</span><span>1/3</span></div>
</section>

<!-- ===== Alternate cover, red ===== -->
<section class="page theme-red col-2 row-3">
  <div class="band band-grey"></div>
  <div class="topline dark"><span>5/30/23, 10:23 AM</span><span>Investment Analysis</span></div>
  <div class="brand-name brand-center"><span class="dot"></span>MERIDIAN REALTY</div>
  <h1 class="title title-center">Investment Analysis<span class="addr">412 Larkfield</span><span class="sub">15-Plex of 1bd/1bth Apartments</span></h1>
  <div class="photos photos-alt">
    <span class="photo ph-house" role="img" aria-label="Property exterior at dusk"></span>
    <span class="photo ph-kitchen" role="img" aria-label="Kitchen interior"></span>
    <span class="photo ph-dining" role="img" aria-label="Dining area interior"></span>
  </div>
  <div class="about" style="left:38px;top:330px;width:150px"><div class="label">About the property</div><p>Lorem ipsum is a placeholder text commonly used to demonstrate the visual form of a document or a typeface without relying on meaningful content.</p><p>Lorem ipsum is a placeholder text commonly used to demonstrate the visual form of a document or a typeface</p></div>
  <div class="map map-alt" role="img" aria-label="Map showing property location"></div>
  <div class="box box-agent"><span class="avatar" role="img" aria-label="Agent headshot"></span><div class="name">Dana Whitlow</div><div>admin1</div><div>(555) 014-2290</div><div>dana@meridian.example</div></div>
  <div class="box box-disc"><strong>DISCLAIMER</strong>In publishing and graphic design, Lorem ipsum is a placeholder text commonly used to demonstrate the visual form of a document or a typeface</div>
  <div class="footer"><span>https://reports.example.com/r/115</span><span>1/3</span></div>
</section>

</div>
</body>
</html>
```